Vantoq Business Card Project showing the logo and a marbo image on the rear

Design a whacky but professional business card, the logo is for the front and the Marbo image is for the rear. Happy to consider other open source Marbo Images if the designer wants to select one from the web. Vantoq is a competitor to OMB.com.au and Pellory.com.au and is based around every property in Australia

Target Market(s)

Business

Contact Information for Business Card

Name, Title, Email, Web, Phone Number

Font styles to use
Other font styles liked:
• avenir

Requirements
Must have
• Image on Back logo on front
Nice to have
• Happy to consider other images on rear, preftably Colin Marbo. Image supplied I own, we can use open source other Marbo Images

```html
<!DOCTYPE html>
<html lang="en">
<head>
<meta charset="utf-8">
<title>Vantoq Business Card</title>
<link href="https://fonts.googleapis.com/css2?family=Montserrat:wght@400;500;700;800&display=swap" rel="stylesheet">
<style>
  :root {
    --backdrop: #b0b1ab;
    --card: #1f1f1f;
    --card-deep: #141414;
    --accent: #f28c1e;
    --ink-light: #ffffff;
    --ink-soft: #e6e6e6;
  }
  * { margin: 0; padding: 0; box-sizing: border-box; }
  html, body {
    width: 1200px; height: 801px; overflow: hidden;
    background: var(--backdrop);
    font-family: "Montserrat", Arial, sans-serif;
  }
  .stage {
    position: relative; width: 1200px; height: 801px;
    display: flex; align-items: center; justify-content: center; gap: 60px;
  }
  .card {
    position: relative; width: 525px; height: 300px;
    background: var(--card);
    border-radius: 26px;
    border-bottom: 4px solid var(--accent);
    box-shadow: 0 14px 30px rgba(0,0,0,0.28);
    overflow: hidden;
  }
  /* front */
  .brand {
    position: absolute; top: 62px; left: 228px;
    display: flex; align-items: center; gap: 12px;
  }
  .brand-square {
    width: 30px; height: 30px; background: var(--accent); border-radius: 4px;
  }
  .brand-name {
    font-weight: 800; font-size: 46px; color: var(--ink-light); letter-spacing: 0.5px;
  }
  .divider {
    position: absolute; left: 108px; right: 40px; top: 190px;
    height: 1px; background: var(--accent);
  }
  .person { position: absolute; left: 62px; top: 132px; }
  .person-name {
    font-weight: 500; font-size: 19px; color: var(--accent); letter-spacing: 0.5px;
  }
  .person-title {
    font-size: 15px; color: var(--ink-soft); margin-top: 2px;
  }
  .contacts { position: absolute; left: 106px; top: 205px; list-style: none; }
  .contacts li {
    display: flex; align-items: center; gap: 8px;
    font-size: 15px; color: var(--ink-soft); line-height: 24px;
  }
  .contacts svg { width: 11px; height: 11px; flex: none; }
  .edge-tab {
    position: absolute; left: 0; bottom: 38px; width: 4px; height: 28px; background: var(--accent);
  }
  /* back */
  .pattern-field {
    position: absolute; inset: 0;
    background: radial-gradient(circle at 35% 60%, #2a2a2a 0%, var(--card) 45%, var(--card-deep) 100%);
  }
  .back-mark {
    position: absolute; top: 50%; left: 50%; transform: translate(-50%, -50%);
    display: flex; align-items: center; gap: 10px;
    background: var(--card); padding: 10px 16px; border-radius: 8px;
  }
  .back-mark .brand-square { width: 22px; height: 22px; }
  .back-mark .brand-name { font-size: 30px; }
</style>
</head>
<body>
<main class="stage">
  <section class="card card-front">
    <div class="brand">
      <span class="brand-square"></span>
      <span class="brand-name">Vantoq</span>
    </div>
    <div class="person">
      <p class="person-name">DANIEL HARROW</p>
      <p class="person-title">Director</p>
    </div>
    <div class="divider"></div>
    <ul class="contacts">
      <li>
        <svg viewBox="0 0 12 12"><path d="M3 1 L5 3.5 L4 4.8 Q5.5 7.5 7.2 8 L8.5 7 L11 9 L9.5 11 Q4 10.5 1 3 Z" fill="var(--accent)"/></svg>
        432-555-0148
      </li>
      <li>
        <svg viewBox="0 0 12 12"><rect x="1" y="2.5" width="10" height="7" fill="none" stroke="var(--accent)" stroke-width="1.2"/><path d="M1 2.5 L6 6.5 L11 2.5" fill="none" stroke="var(--accent)" stroke-width="1.2"/></svg>
        info@vantoq.com.au
      </li>
      <li>
        <svg viewBox="0 0 12 12"><circle cx="6" cy="6" r="5" fill="none" stroke="var(--accent)" stroke-width="1.2"/><ellipse cx="6" cy="6" rx="2.2" ry="5" fill="none" stroke="var(--accent)" stroke-width="1"/><path d="M1 6 H11" stroke="var(--accent)" stroke-width="1"/></svg>
        www.vantoq.com.au
      </li>
    </ul>
    <span class="edge-tab"></span>
  </section>

  <section class="card card-back">
    <div class="pattern-field" role="img" aria-label="Embossed repeating brand pattern across the card back"></div>
    <div class="back-mark">
      <span class="brand-square"></span>
      <span class="brand-name">Vantoq</span>
    </div>
  </section>
</main>
</body>
</html>
```